Elevating our current Business Card Design

We want to elevate our current business card with a new design to look like a zenith 300 company. We are a premium lubricant distributor (oil and grease).
We need 2 versions, version 1 is as per the uploaded a copy of our current business card with the English version.
For our Chinese version we need to use the front to be English in English and have the back of the card designed exactly like the front for all info to be in Chinese.
The design template needs to be such that we can amend the template with adding different information for each person's card.
The background colour of the card can be changed- we just need to clearly see all information on the card and logos.
The QJR and Ember steady logos cannot have any colour or display changes- only use the logos attached.
All logos need to be included and all information from the attached current card

```html
<!DOCTYPE html>
<html lang="en">
<head>
<meta charset="utf-8">
<title>Orvane Business Card</title>
<link rel="stylesheet" href="https://fonts.googleapis.com/css2?family=Open+Sans:wght@400;600;700;800&display=swap">
<style>
  :root {
    --stage: #232323;
    --card: #1f1f22;
    --red: #ec2a24;
    --red-deep: #a5161c;
    --gold: #f4be2c;
    --gold-deep: #d39a25;
    --silver: #c9c9cc;
    --white: #ffffff;
    --badge-orange: #f07a22;
    --badge-grey: #8a8a8e;
    --dots: #3a3430;
  }
  * { box-sizing: border-box; margin: 0; padding: 0; }
  html, body { width: 1200px; height: 780px; overflow: hidden; }
  body {
    background: var(--stage);
    font-family: "Open Sans", Arial, sans-serif;
    color: var(--white);
    position: relative;
  }
  .card {
    position: absolute;
    top: 235px;
    width: 540px;
    height: 310px;
    background: var(--card);
    border-radius: 16px;
    overflow: hidden;
    box-shadow: 0 14px 30px rgba(0,0,0,.55);
  }
  .card--front { left: 40px; }
  .card--back { left: 620px; }
  .card__bands { position: absolute; left: 0; bottom: 0; width: 540px; height: 110px; }

  .brand {
    position: absolute;
    display: flex;
    align-items: center;
    gap: 14px;
    font-weight: 800;
    color: var(--red);
    letter-spacing: 1px;
  }
  .brand__dot { border-radius: 50%; background: var(--gold); }
  .card--front .brand { left: 120px; top: 70px; font-size: 64px; }
  .card--front .brand__dot { width: 44px; height: 44px; }
  .card--back .brand { left: 44px; top: 100px; font-size: 46px; }
  .card--back .brand__dot { width: 32px; height: 32px; }

  .badges { position: absolute; left: 0; top: 0; width: 540px; height: 310px; }
  .badge-seal { position: absolute; width: 30px; height: 30px; border-radius: 50%; background: var(--badge-orange); box-shadow: 0 0 0 4px var(--card), 0 0 0 6px var(--badge-grey); }
  .badge-member { position: absolute; left: 26px; top: 244px; width: 52px; height: 26px; border-radius: 13px 13px 4px 4px; background: var(--white); }
  .partner-box {
    position: absolute; left: 150px; top: 226px;
    border: 2px solid var(--red); border-radius: 4px;
    padding: 4px 8px; font-size: 8px; font-weight: 700; color: var(--red);
    line-height: 1.15; width: 118px;
  }
  .partner-tag {
    position: absolute; left: 272px; top: 200px;
    background: var(--red); border-radius: 3px;
    padding: 5px 10px; font-size: 10px; font-weight: 700; color: var(--white);
    line-height: 1.2;
  }

  .divider { position: absolute; left: 250px; top: 70px; width: 1px; height: 140px; background: linear-gradient(var(--card), var(--silver), var(--card)); transform: rotate(-18deg); }
  .dot-field { position: absolute; left: 270px; top: 20px; width: 260px; height: 200px; border-radius: 50%; background: radial-gradient(ellipse at center, var(--dots), var(--card) 70%); }
  .contact { position: absolute; left: 300px; top: 40px; }
  .contact__name { font-size: 26px; font-weight: 700; color: var(--red); line-height: 1.1; }
  .contact__role { font-size: 13px; font-weight: 600; margin-bottom: 10px; }
  .contact__list { list-style: none; font-size: 12px; line-height: 1.55; }
  .contact__list li { display: flex; align-items: center; gap: 8px; }
  .contact__list svg { width: 12px; height: 12px; flex: none; }
  .address { position: absolute; left: 150px; top: 222px; font-size: 13px; font-weight: 600; }
</style>
</head>
<body>

<section class="card card--front" aria-label="Card front">
  <div class="brand"><span class="brand__dot"></span>Orvane</div>

  <svg class="card__bands" viewBox="0 0 540 110" aria-hidden="true">
    <defs>
      <linearGradient id="redBand" x1="0" x2="1"><stop offset="0" stop-color="var(--red)"/><stop offset="1" stop-color="var(--red-deep)"/></linearGradient>
      <linearGradient id="goldBand" x1="0" x2="1"><stop offset="0" stop-color="var(--gold)"/><stop offset="1" stop-color="var(--gold-deep)"/></linearGradient>
    </defs>
    <polygon points="300,40 540,8 540,28 320,58" fill="url(#redBand)"/>
    <polygon points="0,104 290,64 310,70 0,110" fill="url(#goldBand)"/>
  </svg>

  <div class="badges">
    <span class="badge-member" role="img" aria-label="Ember steady network member badge"></span>
    <span class="badge-seal" style="left:106px;top:240px" role="img" aria-label="QJR certification badge"></span>
    <div class="partner-box">ORVANE LUBRICANT DISTRIBUTORS</div>
    <div class="partner-tag">KESTREL<br>PREMIUM LUBRICANTS</div>
    <span class="badge-seal" style="left:420px;top:196px" role="img" aria-label="QJR certification badge"></span>
    <span class="badge-seal" style="left:470px;top:190px" role="img" aria-label="QJR certification badge"></span>
  </div>
</section>

<section class="card card--back" aria-label="Card back">
  <div class="dot-field" role="img" aria-label="Soft dotted decoration"></div>
  <div class="brand"><span class="brand__dot"></span>Orvane</div>
  <span class="divider"></span>

  <div class="contact">
    <p class="contact__name">Mara Quinlan</p>
    <p class="contact__role">Administration Executive</p>
    <ul class="contact__list">
      <li><svg viewBox="0 0 12 12"><path d="M2 1h3l1 3-2 1a7 7 0 0 0 3 3l1-2 3 1v3c-6 0-9-3-9-9z" fill="var(--red)"/></svg>1300 204 771</li>
      <li><svg viewBox="0 0 12 12"><rect x="3" y="0.5" width="6" height="11" rx="1" fill="none" stroke="var(--red)"/></svg>+61 412 806 330</li>
      <li><svg viewBox="0 0 12 12"><rect x="1" y="4" width="10" height="7" fill="var(--red)"/><rect x="3" y="1" width="6" height="4" fill="none" stroke="var(--red)"/></svg>+61 8 9044 2615</li>
      <li><svg viewBox="0 0 12 12"><circle cx="6" cy="6" r="5" fill="var(--red)"/></svg>www.orvanesupply.com</li>
      <li><svg viewBox="0 0 12 12"><rect x="1" y="3" width="10" height="7" fill="none" stroke="var(--red)"/><path d="M1 3l5 4 5-4" fill="none" stroke="var(--red)"/></svg>mara.q@orvanesupply.com</li>
    </ul>
  </div>

  <p class="address">48 Harbour Lane Eastfield, WA 6090</p>

  <svg class="card__bands" viewBox="0 0 540 110" aria-hidden="true">
    <defs>
      <linearGradient id="redBand2" x1="0" x2="1"><stop offset="0" stop-color="var(--red)"/><stop offset="1" stop-color="var(--red-deep)"/></linearGradient>
      <linearGradient id="goldBand2" x1="0" x2="1"><stop offset="0" stop-color="var(--gold)"/><stop offset="1" stop-color="var(--gold-deep)"/></linearGradient>
    </defs>
    <polygon points="300,60 540,28 540,48 320,78" fill="url(#redBand2)"/>
    <polygon points="0,104 290,74 310,80 0,110" fill="url(#goldBand2)"/>
  </svg>
</section>

</body>
</html>
```